Little Dazzle Wren Flyer

Hi, Thank you for doing such a great job! I would like you to work with me on this flyer but give me a couple of option designs that I could choose from. To be honest im still a hundred per cent in what contents I want on this flyer but here it is. This is a double sided flyer!

One side is Little Dazzle Wren and the other side is Coastal Roving Face & Body.

I was thinking with Little Dazzle Wren I could have some slogan like Lets Party.... (something like that) I was thinking balloons etc. Also I have 4 boxes that I want to use with pictures with a little brief description in paragrapth order.

I don't have the description yet but will be writing it this weekend. I can upload later as I would like to get the design started. I would like you to use Spoil Us Soirees, Lovely in Lilac Tutu Party, Sir Groove Street Jam Party and lastly Garden Cups Buzzy Wren Party. You will see I have attached a photo of a ballet girl, hip hop photo, high tea photo and a pamper photo of two girls. These pictures are used in conjunction with each party theme. I will also need my number in large and including another number as well (I think) I will get back to that. as well as a email address ( I will also get back to you with that) my web address and a facebook thing to like.

Coastal Roving Face & Body

Basically this side is about our Adult Pamper Party. I would like to say something that I will forward to you. If wil only be breif, and a picture and promoting how the host received a free skin care kit of choice valued at $180 for hosting etc and maybe down the bottom of the page I could also in point form put my other services. I If you can start on Little Dazzle Wren that would be a good start and I can get back to you with more information on this one. This is a gift to me and they want me to pay for it now when I wasn't prepared with all my information for you. so please forgive me.

I was thinking this may be just for a A5 size but at some stage I will print both on a4 as well as poster size if this is possible.

You are probably confused as I am too. I will forward little dazzle wren pictures in order and then one for Coastal roving face and body (but I have another one coming on Monday) I will email you as necessary with more of my wording I need.

I know less is better so im trying not to put to much for Coastal roving but I think really like to talk a bit more about party options for little d w .

I will be going onto piclarder now to see if I can find another appro photo for pamper parties then apposed to one I sent. Im sure you will be not understanding my contents as im totally not prepared but I hope you can get started . And once again thank you very very much.

Target Market(s)

parents with children for little dazzle wren and women over the age of thirty for adult pamper parties on the opposite flyer

Industry/Entity Type

Adult

Requirements
Must have
• the last image of lady with mask on half her face . I would like that picture on Coastal rovng face and body side for pamper parties please. you can choose to ignore the girl with champagn glass if you wish as I need to put a picture of what thehost gets and I will upload that one within the next two days.
Should not have
• under the logo Coastal roving face and body I want the words healthier looking skin taken out please

```html
<!DOCTYPE html>
<html lang="en">
<head>
<meta charset="utf-8">
<title>Little Dazzle Wren Flyer</title>
<link href="https://fonts.googleapis.com/css2?family=Gochi+Hand&display=swap" rel="stylesheet">
<style>
  :root{
    --backdrop:#f2f2f2;
    --hot-pink:#ec008c;
    --panel-pink:#e8579b;
    --panel-cyan:#0eb0ec;
    --panel-indigo:#2f3b8f;
    --panel-green:#3ba648;
    --strip-black:#000;
    --paper:#fff;
    --brand-yellow:#ffe600;
    --type:'Gochi Hand', cursive;
  }
  *{margin:0;padding:0;box-sizing:border-box;}
  html,body{width:1200px;height:1000px;overflow:hidden;}
  body{background:var(--backdrop);position:relative;font-family:var(--type);}

  .flyer{position:absolute;overflow:hidden;}
  .flyer--portrait{left:53px;top:206px;width:441px;height:626px;}
  .flyer--landscape{left:524px;top:299px;width:625px;height:441px;background:var(--paper);}

  .panel{position:absolute;}
  .panel--pink{background:var(--panel-pink);}
  .panel--cyan{background:var(--panel-cyan);}
  .panel--indigo{background:var(--panel-indigo);}
  .panel--green{background:var(--panel-green);}

  .party-title{position:absolute;z-index:2;color:#fff;font-size:24px;line-height:29px;}

  .photo{position:absolute;z-index:1;}
  .photo--pamper{background:linear-gradient(135deg,#f3d9d3,#e7c3b6 60%,#d8a99c);}
  .photo--tea{background:linear-gradient(160deg,#8fbf5a,#e9e2dc 55%,#f4a06a);}
  .photo--ballet{background:linear-gradient(150deg,#3f6b2e,#e8d6d8 55%,#f2e8ea);}
  .photo--dance{background:linear-gradient(180deg,#8fd6cd,#5fbfb3 60%,#2b2b2b);}

  /* portrait side */
  .side-strip{position:absolute;left:0;top:0;width:120px;height:626px;background:var(--strip-black);overflow:hidden;}
  .headline--vertical{position:absolute;left:0;bottom:0;width:120px;height:490px;
    writing-mode:vertical-rl;transform:rotate(180deg);color:var(--hot-pink);
    font-size:100px;line-height:120px;text-align:left;white-space:nowrap;overflow:hidden;}

  .brand{position:absolute;text-align:center;}
  .brand__row{display:flex;align-items:center;justify-content:center;gap:4px;}
  .brand__dot{width:10px;height:10px;border-radius:50%;background:var(--brand-yellow);flex:none;}
  .brand__name{color:var(--hot-pink);font-size:13px;line-height:15px;white-space:nowrap;}
  .brand__contact{color:var(--hot-pink);font-size:7px;line-height:10px;margin-top:6px;white-space:nowrap;}
  .brand__phone{display:flex;align-items:center;justify-content:center;gap:3px;}
  .brand--strip{left:2px;top:52px;width:116px;}
  .brand--header{left:478px;top:40px;width:140px;}
  .brand--header .brand__name{font-size:14px;}

  /* landscape side */
  .headline--horizontal{position:absolute;left:4px;top:-8px;color:var(--hot-pink);font-size:96px;line-height:120px;white-space:nowrap;}
</style>
</head>
<body>

<section class="flyer flyer--portrait">
  <div class="side-strip">
    <div class="brand brand--strip">
      <div class="brand__row"><span class="brand__name">Little Dazzle Wren</span><span class="brand__dot"></span></div>
      <div class="brand__contact">
        <div class="brand__phone"><svg width="8" height="8" viewBox="0 0 10 10"><path d="M2 1l2 2-1 1.5a6 6 0 0 0 2.5 2.5L7 6l2 2-1.5 1.5C4.5 9 1 5.5.5 2.5z" fill="#ec008c"/></svg>0400 55 1234</div>
        <div>www.littledazzlewren.com.au</div>
      </div>
    </div>
    <div class="headline--vertical">Got Party?</div>
  </div>

  <div class="panel panel--pink" style="left:120px;top:0;width:321px;height:144px;">
    <div class="photo photo--pamper" role="img" aria-label="Two girls in headbands wearing face masks, laughing" style="left:16px;top:8px;width:144px;height:129px;"></div>
    <div class="party-title" style="left:170px;top:16px;width:140px;">Spoil Us<br>Soirees</div>
  </div>
  <div class="panel panel--cyan" style="left:120px;top:146px;width:321px;height:164px;">
    <div class="party-title" style="left:12px;top:18px;width:124px;">Garden Cups Buzzy Wren Party</div>
    <div class="photo photo--tea" role="img" aria-label="High tea table with cupcakes on a tiered stand and pink milk bottles" style="left:139px;top:8px;width:172px;height:151px;"></div>
  </div>
  <div class="panel panel--indigo" style="left:120px;top:312px;width:321px;height:166px;">
    <div class="photo photo--ballet" role="img" aria-label="Little girls in pink ballet tutus eating cupcakes" style="left:16px;top:6px;width:104px;height:156px;"></div>
    <div class="party-title" style="left:126px;top:12px;width:180px;">Lovely in<br>Lilac Tutu<br>Party</div>
  </div>
  <div class="panel panel--green" style="left:120px;top:480px;width:321px;height:146px;">
    <div class="party-title" style="left:14px;top:12px;width:204px;">Sir Groove Street<br>Jam Party</div>
    <div class="photo photo--dance" role="img" aria-label="Breakdancer balancing on one hand" style="left:224px;top:6px;width:89px;height:133px;"></div>
  </div>
</section>

<section class="flyer flyer--landscape">
  <div class="headline--horizontal">Got Party?</div>
  <div class="brand brand--header">
    <div class="brand__row"><span class="brand__name">Little Dazzle Wren</span><span class="brand__dot"></span></div>
    <div class="brand__contact">
      <div class="brand__phone"><svg width="8" height="8" viewBox="0 0 10 10"><path d="M2 1l2 2-1 1.5a6 6 0 0 0 2.5 2.5L7 6l2 2-1.5 1.5C4.5 9 1 5.5.5 2.5z" fill="#ec008c"/></svg>0400 55 1234</div>
      <div>www.littledazzlewren.com.au</div>
    </div>
  </div>

  <div class="panel panel--pink" style="left:0;top:111px;width:310px;height:164px;">
    <div class="photo photo--pamper" role="img" aria-label="Two girls in headbands wearing face masks, laughing" style="left:4px;top:4px;width:172px;height:156px;"></div>
    <div class="party-title" style="left:180px;top:10px;width:125px;">Spoil Us<br>Soirees</div>
  </div>
  <div class="panel panel--indigo" style="left:312px;top:111px;width:313px;height:162px;">
    <div class="photo photo--ballet" role="img" aria-label="Little girls in pink ballet tutus eating cupcakes" style="left:4px;top:4px;width:105px;height:154px;"></div>
    <div class="party-title" style="left:111px;top:10px;width:190px;">Lovely in<br>Lilac Tutu<br>Party</div>
  </div>
  <div class="panel panel--cyan" style="left:0;top:276px;width:310px;height:165px;">
    <div class="party-title" style="left:8px;top:14px;width:114px;">Garden Cups Buzzy Wren Party</div>
    <div class="photo photo--tea" role="img" aria-label="High tea table with cupcakes on a tiered stand and pink milk bottles" style="left:126px;top:2px;width:182px;height:160px;"></div>
  </div>
  <div class="panel panel--green" style="left:312px;top:276px;width:313px;height:165px;">
    <div class="party-title" style="left:12px;top:12px;width:184px;">Sir Groove Street Jam Party</div>
    <div class="photo photo--dance" role="img" aria-label="Breakdancer balancing on one hand" style="left:202px;top:3px;width:108px;height:159px;"></div>
  </div>
</section>

</body>
</html>
```